Business card design Needed for new logo / Construction business, home extensions and new builds

We need a business card design using our new logo files which i will attach to this project :)

We are a small construction business specialising in home extensions, new builds and property development. We are very ambitious and would appreciate professional and elegant designs for our new business card.

Very serious about using the services on MakerQuarry and recently acquired our new logo from here :)

Please get involved, i will feedback when i can as i am very busy but can respond daily, thanks

Target Market(s)

People that want to build onto their houses, new building developments or adding too their existing property

Industry/Entity Type

Construction

Contact Information for Business Card

Renwick Tolliver Construction, Lionel Ashby (Managing Director), Tel 07822254961, email - info@renwick-tolliver, www.renwick-tolliver.co.uk

Colors

Designer to choose colors to be used in the design.

Requirements
Must have
• I like a deep grey on the back please. A lot of you have provided black from and back, try mixing things up a little. The black looks cool 😎 Thanks

```html
<!DOCTYPE html>
<html lang="en">
<head>
<meta charset="utf-8">
<title>Renwick Tolliver Construction – Business Card</title>
<link rel="stylesheet" href="https://fonts.googleapis.com/css2?family=Lato:wght@400;700&display=swap">
<style>
  :root {
    --page-bg: #1c1c1c;
    --card-dark: #030303;
    --card-mid: #1e1e1e;
    --back-mid: #454545;
    --back-edge: #2e2e2e;
    --gold: #d0921a;
    --gold-light: #f6cf75;
    --gold-deep: #c8880f;
    --silver: #c9ccd0;
    --silver-dark: #8d9297;
    --text-grey: #b5b7ba;
    --text-light: #e6e6e6;
  }
  * { margin: 0; padding: 0; box-sizing: border-box; }
  html, body { width: 1200px; height: 1200px; overflow: hidden; }
  body {
    background: var(--page-bg);
    font-family: "Lato", sans-serif;
    position: relative;
  }
  .card {
    position: absolute;
    left: 250px;
    width: 700px;
    height: 400px;
    border-radius: 20px;
    overflow: hidden;
  }
  .card--front {
    top: 170px;
    background: radial-gradient(ellipse at 50% 50%, var(--card-mid) 0%, var(--card-dark) 70%);
  }
  .card--back {
    top: 630px;
    background: radial-gradient(ellipse at 50% 45%, var(--back-mid) 0%, var(--back-edge) 75%);
  }

  /* Front */
  .brand-mark {
    position: absolute;
    left: 90px;
    top: 150px;
    width: 200px;
    display: flex;
    align-items: center;
    justify-content: center;
    gap: 10px;
    color: var(--gold);
    font-weight: 700;
    font-size: 22px;
    line-height: 1.2;
    text-align: center;
  }
  .brand-mark__square {
    width: 14px; height: 14px;
    background: var(--gold);
    flex: none;
  }
  .divider {
    position: absolute;
    left: 327px;
    top: 89px;
    width: 2px;
    height: 192px;
    background: var(--gold-deep);
  }
  .contact {
    position: absolute;
    left: 365px;
    top: 82px;
  }
  .contact__name {
    color: var(--gold);
    font-size: 29px;
    font-weight: 400;
    letter-spacing: 0.2px;
    line-height: 1.1;
  }
  .contact__title {
    color: var(--text-grey);
    font-size: 20px;
    margin-top: 2px;
  }
  .contact__company {
    color: var(--text-light);
    font-size: 17px;
    font-weight: 700;
    margin-top: 12px;
  }
  .contact__address {
    color: var(--text-light);
    font-size: 17px;
    line-height: 25px;
    margin-top: 3px;
  }
  .contact__line {
    display: flex;
    align-items: center;
    gap: 12px;
    color: var(--text-light);
  }
  .contact__line svg { width: 15px; height: 15px; fill: var(--gold); flex: none; }
  .contact__phone { font-size: 20px; margin-top: 10px; }
  .contact__email { font-size: 17px; margin-top: 6px; }

  .web-band {
    position: absolute;
    left: 0; bottom: 0;
    width: 700px; height: 35px;
  }
  .web-band svg { position: absolute; inset: 0; }
  .web-band__url {
    position: absolute;
    left: 0; width: 575px;
    top: 0; height: 35px;
    line-height: 35px;
    text-align: center;
    font-size: 16px;
    letter-spacing: 2.6px;
    color: #1a1206;
  }
  .web-band__url strong { font-weight: 700; }

  /* Back */
  .back-brand {
    position: absolute;
    inset: 0;
    display: flex;
    flex-direction: column;
    align-items: center;
    justify-content: center;
    gap: 22px;
    padding-top: 20px;
  }
  .back-brand__square {
    width: 40px; height: 40px;
    background: var(--gold);
  }
  .back-brand__name {
    color: var(--gold);
    font-weight: 700;
    font-size: 36px;
    letter-spacing: 3px;
    text-transform: uppercase;
    text-align: center;
    line-height: 1.25;
  }
</style>
</head>
<body>

<section class="card card--front">
  <div class="brand-mark">
    <span class="brand-mark__square"></span>
    <span>Renwick<br>Tolliver</span>
  </div>

  <div class="divider"></div>

  <div class="contact">
    <h1 class="contact__name">LIONEL ASHBY</h1>
    <p class="contact__title">Managing Director</p>
    <p class="contact__company">Renwick Tolliver Construction</p>
    <p class="contact__address">Your Address, City<br>State, Zip 1235</p>
    <p class="contact__line contact__phone">
      <svg viewBox="0 0 24 24" aria-hidden="true"><path d="M6.6 10.8a15.2 15.2 0 0 0 6.6 6.6l2.2-2.2a1 1 0 0 1 1-.25 11.4 11.4 0 0 0 3.6.57 1 1 0 0 1 1 1V20a1 1 0 0 1-1 1A17 17 0 0 1 3 4a1 1 0 0 1 1-1h3.5a1 1 0 0 1 1 1c0 1.25.2 2.45.57 3.57a1 1 0 0 1-.25 1z"/></svg>
      07822254961
    </p>
    <p class="contact__line contact__email">
      <svg viewBox="0 0 24 24" aria-hidden="true"><path d="M2 5h20v14H2z M3.5 6.5 12 13l8.5-6.5" fill="var(--gold)" stroke="#111" stroke-width="1.4"/></svg>
      info@renwick-tolliver.co.uk
    </p>
  </div>

  <div class="web-band">
    <svg width="700" height="35" viewBox="0 0 700 35" aria-hidden="true">
      <defs>
        <linearGradient id="bandGold" x1="0" x2="1" y1="0" y2="0">
          <stop offset="0" stop-color="#c8860e"/>
          <stop offset="0.5" stop-color="#f6cf75"/>
          <stop offset="1" stop-color="#d69a22"/>
        </linearGradient>
        <linearGradient id="bandSilver" x1="0" x2="1" y1="0" y2="0">
          <stop offset="0" stop-color="#f0f1f2"/>
          <stop offset="1" stop-color="#8d9297"/>
        </linearGradient>
      </defs>
      <polygon points="0,0 620,0 593,35 0,35" fill="url(#bandGold)"/>
      <polygon points="620,0 632,0 605,35 593,35" fill="#000"/>
      <polygon points="632,0 700,0 700,35 605,35" fill="url(#bandSilver)"/>
    </svg>
    <p class="web-band__url">WWW.<strong>RENWICK-TOLLIVER</strong>.CO.UK</p>
  </div>
</section>

<section class="card card--back">
  <div class="back-brand">
    <span class="back-brand__square"></span>
    <p class="back-brand__name">Renwick Tolliver<br>Construction</p>
  </div>
</section>

</body>
</html>
```